Luxury sell sheet flyer Design

We need two luxury/premium looking sales flyer - one for luxury and one for travel-

Please find flyers from last year (2015) attached. Please copy the pictures and the look and feel (and colors), and use the content form the 2016 documents.

These flyers will be used for corporate subscription sales and targetted at CMOs and Marketing heads. As such they should convey a very premium look and feel.

Please provide in format that we can make text edits in later.

USA, UK, Asia

Travel

Serif

• Good copyright free pictures, no clip art, that show a very premium look and feel for a corporate flyer
• clean feel, not cluttered
• clip art

```html
<!DOCTYPE html>
<html lang="en">
<head>
<meta charset="utf-8">
<title>Affluent Insights Subscription 2016</title>
<link rel="stylesheet" href="https://fonts.googleapis.com/css2?family=Tinos:ital,wght@0,400;0,700;1,400;1,700&display=swap">
<style>
  :root {
    --ink: #111111;
    --lavender: #e6ddf3;
    --lavender-deep: #cdbfe6;
    --band: #6a3f9e;
    --rule: #333333;
    --faint: rgba(255,255,255,0.55);
    --badge: #c9c9cf;
  }
  * { margin: 0; padding: 0; box-sizing: border-box; }
  html, body { width: 927px; height: 1200px; overflow: hidden; }
  body {
    position: relative;
    font-family: "Tinos", "Times New Roman", serif;
    font-size: 13.6px;
    line-height: 16.7px;
    color: var(--ink);
    background:
      radial-gradient(ellipse 60% 45% at 55% 35%, #ffffff 0%, rgba(255,255,255,0) 70%),
      linear-gradient(180deg, #f3eff9 0%, var(--lavender) 55%, var(--lavender-deep) 100%);
  }
  .block { position: absolute; }
  ol { padding-left: 28px; }
  b, .bold { font-weight: 700; }
  .brand-watermark {
    position: absolute; left: 470px; top: 150px;
    font-size: 54px; line-height: 56px; color: var(--faint);
    letter-spacing: 2px; white-space: nowrap;
  }
  .intro { left: 15px; top: 20px; width: 440px; }
  .section-title { font-weight: 700; font-size: 14.5px; letter-spacing: 0.2px; }
  .reports { left: 22px; top: 316px; width: 420px; }
  .cat-head { left: 24px; top: 398px; font-style: italic; font-weight: 700; }
  .cat-table {
    left: 30px; top: 418px; width: 392px; border-collapse: collapse;
    font-size: 12.4px; line-height: 14px;
  }
  .cat-table td { border: 1px solid var(--rule); padding: 3px 5px; height: 20px; }
  .cat-table td:first-child { width: 240px; }
  .rule { position: absolute; background: var(--rule); }
  .analytics { left: 36px; top: 535px; width: 402px; }
  .analytics .indent { padding-left: 42px; }
  .right-top { left: 447px; top: 20px; width: 470px; }
  .defs-label { left: 462px; top: 320px; width: 150px; font-weight: 700; font-size: 12.4px; line-height: 14px; }
  .defs-arrow { position: absolute; left: 648px; top: 326px; }
  .hhi-table {
    left: 652px; top: 245px; width: 242px; border-collapse: collapse;
    font-size: 12px; line-height: 14px; font-weight: 700; background: #ffffff;
  }
  .hhi-table th { text-align: left; padding: 4px 7px; height: 23px; background: transparent; }
  .hhi-table td { border: 1px solid #bdbdbd; padding: 3px 7px; height: 23px; }
  .hhi-table td:first-child { width: 105px; }
  .right-bottom { left: 447px; top: 446px; width: 472px; }
  .right-bottom p { margin: 0; }
  .gap { height: 6px; }
  .level-item { padding-left: 16px; }
  .press-note {
    left: 438px; top: 1150px; width: 230px; font-size: 7.5px; line-height: 9px; font-weight: 700;
  }
  .press-strip {
    left: 676px; top: 1118px; width: 246px; height: 58px; background: #ffffff;
    display: grid; grid-template-columns: repeat(6, 1fr); gap: 5px; padding: 6px;
  }
  .press-strip span { background: var(--badge); height: 9px; border-radius: 1px; }
  .bottom-band { left: 0; top: 1183px; width: 927px; height: 17px; background: var(--band); }
</style>
</head>
<body>

<div class="brand-watermark" aria-hidden="true">Meridian Research &amp; Strategy</div>

<section class="block intro">
  <p class="bold">The subscription service comprises of four offerings:</p>
  <ol>
    <li>Affluent Consumer and Luxury Brand Reports (semi-annual)</li>
    <li>Quarterly Luxury Leader Roundtables with Senior Executives from the Luxury World</li>
    <li>Custom Tabulations of Data (semi-annual)</li>
    <li>Semi-annual Brainstorming Sessions with Meridian Experts</li>
  </ol>
  <p>And provides answers to these key questions, and more:</p>
  <ol>
    <li>Will affluent shoppers be spending more on luxury watches?</li>
    <li>Will their next handbag sport a subdued design or feature brand logos?</li>
    <li>Is quartz a deal-breaker in the luxury scene?</li>
    <li>How popular are luxury handbag customization services?</li>
    <li>Who are the up and comers to watch out for in the luxury space?</li>
    <li>Which market will be most likely to enjoy luxury goods next year?</li>
    <li>What is the customer profile for affluent consumers who prefer European luxury brands?</li>
    <li>Which sports are the affluent actively participating in nowadays?</li>
  </ol>
</section>

<section class="block reports">
  <h2 class="section-title">AFFLUENT CONSUMER AND LUXURY BRAND REPORTS</h2>
  <p>The 2016 subscription includes two category specific reports per market, one released<br>half-way and the other one at the end of the year.</p>
</section>

<p class="block cat-head">The following luxury product categories are available in each market:</p>
<table class="block cat-table">
  <tr><td>Designer Clothing &amp; Accessories (83 brands)</td><td>Watches (82 brands)</td></tr>
  <tr><td>Jewellery (39 brands)</td><td>Skincare (52 brands)</td></tr>
  <tr><td>Makeup (49 brands)</td><td>Cars (46 brands)</td></tr>
  <tr><td>Alcohol (65 brands, including beer)</td><td></td></tr>
</table>

<div class="rule" style="left:14px; top:307px; width:426px; height:1px;"></div>
<div class="rule" style="left:22px; top:518px; width:415px; height:1px;"></div>
<div class="rule" style="left:436px; top:442px; width:1px; height:77px;"></div>
<div class="rule" style="left:436px; top:442px; width:474px; height:1px;"></div>

<section class="block analytics">
  <p class="bold">Key analytics in the reports include:</p>
  <p><b>-Luxury Brand Index</b> – A tool to help brands understand how well they are meeting the expectation of their potential customers in relation to their competitors in different markets. The index is derived from the importance of different dimensions of luxury on category purchase intent and brands’ ratings on the same dimensions.</p>
  <p><b>-Luxury Brand Media Reach</b> – Gives the brands vital information on how well they are being noticed in the most relevant media touchpoints. This is calculated based on the importance of different media touchpoints for affecting category purchasing and recall of brand recall in the relevant touchpoints.</p>
  <p><b>-Luxury Consumer Segmentation</b> - We have identified unique key luxury consumer types that are different in their motivations and purchase behaviour towards luxury brands. This segmentation will help brands understand their key consumer types in each market.</p>
  <p><b>-Affluent Luxury Consumer Insights</b> – We will have numerous analyses to help you understand and profile affluent consumers in each market, looking at their purchase behaviour, media influences, psychographics, and demographics. Many of the analyses will be trended to understand shifts in consumer preferences. Key topics for the analyses include:</p>
  <p>-Luxury Purchase Triggers</p>
  <p>-Purchase Channels (online and offline)</p>
  <p>-Luxury Categories and Brands Intended to Purchase</p>
  <p>-Luxury Watches In-depth</p>
  <p class="indent">Type preferences: Standard, Chrono, GMT, etc.</p>
  <p class="indent">Jewelled or standard</p>
  <p class="indent">Purpose: Daily use, sports/active, or special occasions</p>
  <p class="indent">Preferred strap type: leather, metal bracelet, NATO</p>
  <p class="indent">Influence of country of manufacture</p>
  <p class="indent">Luxury watches as a gift item</p>
  <p>-Luxury Bags In-depth</p>
  <p class="indent">Bag design trends: multiple logos, single logos, or subdued logos</p>
  <p class="indent">Preferred material</p>
  <p class="indent">Preferred closures: zippered, magnetized, etc.</p>
  <p class="indent">Trending styles: totes, shoulder bags, bowlers, etc.</p>
  <p class="indent">Desire for personalization services</p>
  <p>-Spend and Share of Wallet for Different Luxury Categories</p>
</section>

<section class="block right-top">
  <p>In each market we are focusing on affluent consumers (approximately top-20% of the population based on household income) who are a primary target for luxury goods manufacturers and retailers, and luxury service providers. We are fielding two waves in 2016, and interviewing a total of n=300 affluent consumers in each market (100 of the interviews will be among HNWIs per wave).</p>
  <div class="gap"></div>
  <p>We have four core markets (where trending to last year will be available for some content): <b>• China • Singapore • Hong Kong • USA</b></p>
  <div class="gap"></div>
  <p>Additional markets for 2016 fielding are:<br><b>• South Korea • Japan • France</b></p>
  <p>Other markets, such as,<br><b>UK, India, Indonesia, Malaysia, Thailand, and Taiwan</b> can be added by request.</p>
</section>

<p class="block defs-label">Affluent consumer definitions are as follows:</p>
<svg class="defs-arrow" width="8" height="12" viewBox="0 0 8 12" aria-hidden="true"><path d="M0 0 L8 6 L0 12 Z" fill="#111"/></svg>

<table class="block hhi-table">
  <tr><th>COUNTRY</th><th>Annual HHI</th></tr>
  <tr><td>US</td><td>USD 150,000+</td></tr>
  <tr><td>China</td><td>CNY 270,000+</td></tr>
  <tr><td>Singapore</td><td>SGD 150,000+</td></tr>
  <tr><td>Hong Kong</td><td>HK$ 1,000,000+</td></tr>
  <tr><td>Korea</td><td>KRW 100 million +</td></tr>
  <tr><td>Japan</td><td>JPY 13,500,000+</td></tr>
  <tr><td>France</td><td>EUR 100,000+</td></tr>
</table>

<section class="block right-bottom">
  <p>-Media Touchpoints Relevant to Each Category</p>
  <p>-Psychographics around Luxury Purchase Behaviour</p>
  <p>-Hobbies and Interests &nbsp; • Sports • Fine dining and celebrity restaurants</p>
  <p>Arts and culture &nbsp; -Travel preferences</p>
  <p>-Affluent Consumer Profiles</p>
  <p class="section-title">B. QUARTERLY LUXURY LEADER ROUNDTABLES (with Senior Executives from the Luxury World)</p>
  <p>These are private, invitation-only, informal lunch and evening sessions held quarterly at central premium locations in Hong Kong and Singapore. During these sessions we will share latest findings on affluent luxury consumers and moderate a discussion on topical themes among luxury leaders (including executives from luxury brands and luxury though leaders).</p>
  <div class="gap"></div>
  <p class="section-title">C. CUSTOM TABULATIONS OF DATA</p>
  <p>We will provide a set of tabulations of the data for all basic graphs included in the report with custom cuts (up to 20 banner points), e.g., you target consumer age groups, or consumers who are planning a purchase from your competitive brand set.</p>
  <div class="gap"></div>
  <p class="section-title">D. SEMI-ANNUAL BRAINSTORMING SESSIONS (with Meridian Experts)</p>
  <p>We will facilitate two brainstorming sessions (timed after the release of each of the Affluent Consumer and Luxury Brand Reports). In these two-hour sessions we walk you through the findings from the latest data release, and together with you look at implications the findings have on your specific brand(s), and brainstorm on how your brand can best make us of the findings. These sessions can be held in our or your premises in Singapore or Hong Kong.</p>
  <p>2016 Affluent Insights Subscription Service is category specific and has three optional service levels:</p>
  <div class="gap"></div>
  <p class="bold">Affluent Insights Plus</p>
  <p class="level-item">2 Affluent Consumer and Luxury Brand Reports</p>
  <p class="bold">Affluent Insights Premium</p>
  <p class="level-item">2 Affluent Consumer and Luxury Brand Reports</p>
  <p class="level-item">2 Invitations to Quarterly Luxury Leader Roundtables</p>
  <p class="level-item">1 Set of Custom Tabulations of Data (per market)</p>
  <p class="bold">Affluent Insights Prestige</p>
  <p class="level-item">2 Affluent Consumer and Luxury Brand Reports (Category Specific)</p>
  <p class="level-item">4 Invitations to Quarterly Luxury Leader Roundtables</p>
  <p class="level-item">2 Sets of Custom Tabulations of Data (per market)</p>
  <p class="level-item">2 Semi-annual Brainstorming Sessions (per market) or speaking engagements. (We have spoken at key luxury events with <b>Opulence Review, The Daily Ledger, and National Broadcast</b>.)</p>
</section>

<p class="block press-note">Our research has been featured in international media, such as:</p>
<div class="block press-strip" role="img" aria-label="Media outlet badges">
  <span></span><span></span><span></span><span></span><span></span><span></span>
  <span></span><span></span><span></span><span></span><span></span><span></span>
  <span></span><span></span><span></span><span></span>
</div>

<div class="block bottom-band"></div>

</body>
</html>
```